Targeted Marketing

Postcard will be sent to customers who’ve already been contacted or will be in the next week or two reiterating information found on my website www.bentcedarholdings.example. Trying to keep my company name in the forefront of their mind when it comes time to divest their mineral interests.

```html
<!DOCTYPE html>
<html lang="en">
<head>
<meta charset="utf-8">
<title>Bent Cedar Holdings – Postcard Back</title>
<link href="https://fonts.googleapis.com/css2?family=Montserrat:wght@400;500;700;800&display=swap" rel="stylesheet">
<style>
  :root {
    --brand-red: #e31e24;
    --ink: #1a1a1a;
    --white: #ffffff;
    --rule-grey: #e4e4e4;
    --divider-grey: #d9d9d9;
    --watermark-grey: #e6e6e6;
  }
  * { margin: 0; padding: 0; box-sizing: border-box; }
  html, body { width: 1200px; height: 858px; overflow: hidden; background: var(--white); }
  body { font-family: "Montserrat", sans-serif; color: var(--ink); }
  .postcard { position: relative; width: 1200px; height: 858px; background: var(--white); }

  .brand-name {
    position: absolute; left: 88px; top: 100px;
    display: flex; align-items: center; gap: 12px;
    font-size: 34px; font-weight: 800; color: var(--ink); letter-spacing: -0.5px;
  }
  .brand-square { width: 30px; height: 30px; background: var(--brand-red); }

  .return-address {
    position: absolute; left: 401px; top: 90px;
    font-size: 13.6px; line-height: 16.6px; font-weight: 400; letter-spacing: 0.2px;
  }

  .tagline-band {
    position: absolute; left: 88px; top: 179px; width: 557px; height: 26px;
  }
  .tagline-band svg { position: absolute; inset: 0; }
  .tagline-text {
    position: absolute; left: 0; right: 0; top: 0; line-height: 26px; text-align: center;
    color: var(--white); font-weight: 700; font-size: 13.4px; letter-spacing: 0.2px;
  }

  .stamp-box {
    position: absolute; left: 1008px; top: 84px; width: 104px; height: 130px;
    border: 2px solid var(--ink);
  }

  .perforation {
    position: absolute; left: 511px; top: 234px; width: 4px; height: 554px;
    background-image: radial-gradient(circle, var(--ink) 1.4px, transparent 1.6px);
    background-size: 4px 7.4px; background-repeat: repeat-y;
  }

  .section-heading { position: absolute; top: 428px; font-size: 16.5px; font-weight: 800; }
  .why-sell-heading { right: calc(1200px - 242px); color: var(--brand-red); }
  .value-heading { left: 301px; color: var(--ink); }

  .column-divider {
    position: absolute; left: 272px; top: 419px; width: 3px; height: 343px; background: var(--divider-grey);
  }

  .point { position: absolute; display: flex; align-items: center; font-size: 12.4px; line-height: 15.2px; }
  .point-icon { width: 34px; height: 34px; border-radius: 50%; flex: none; }
  .why-sell .point { right: calc(1200px - 241px); text-align: right; gap: 12px; }
  .why-sell .point-icon { background: var(--brand-red); }
  .value .point { left: 301px; gap: 11px; }
  .value .point-icon { background: var(--ink); }

  .address-rule { position: absolute; left: 601px; height: 3px; background: var(--rule-grey); }

  .watermark-name {
    position: absolute; left: 740px; top: 560px; width: 300px; text-align: center;
    font-size: 40px; font-weight: 800; color: var(--watermark-grey); line-height: 44px;
  }
</style>
</head>
<body>
<main class="postcard">
  <div class="brand-name"><span class="brand-square"></span>Bent Cedar</div>

  <address class="return-address" style="font-style:normal">
    Bent Cedar Holdings LLC<br>
    Attn: Dale R. Whitcomb PO Box 4410<br>
    Mesa Verde, NM 88099 - 555.014.2290<br>
    dale@bentcedarholdings.example
  </address>

  <div class="tagline-band">
    <svg width="557" height="26" viewBox="0 0 557 26"><polygon points="14,0 557,0 541,26 0,26" fill="var(--brand-red)"/></svg>
    <p class="tagline-text">Acquiring Producing and Non-Producing Mineral &amp; Royalty Interests</p>
  </div>

  <div class="stamp-box" aria-label="Stamp area"></div>
  <div class="perforation"></div>

  <h2 class="section-heading why-sell-heading">Why Sell:</h2>
  <section class="why-sell">
    <div class="point" style="top:461px">Immediate<br>Cash<span class="point-icon"></span></div>
    <div class="point" style="top:513px">Monthly Revenue<br>Stream<span class="point-icon"></span></div>
    <div class="point" style="top:564px">Estate<br>Planning<span class="point-icon"></span></div>
    <div class="point" style="top:615px">Tax<br>Reasons<span class="point-icon"></span></div>
    <div class="point" style="top:666px">Risk<span class="point-icon"></span></div>
    <div class="point" style="top:717px">Management<span class="point-icon"></span></div>
  </section>

  <div class="column-divider"></div>

  <h2 class="section-heading value-heading">How We Value:</h2>
  <section class="value">
    <div class="point" style="top:461px"><span class="point-icon"></span>Historical<br>Production</div>
    <div class="point" style="top:513px"><span class="point-icon"></span>Reservoir<br>Analysis</div>
    <div class="point" style="top:564px"><span class="point-icon"></span>Operator<br>Reputation</div>
    <div class="point" style="top:615px"><span class="point-icon"></span>Future<br>Drilling</div>
    <div class="point" style="top:666px"><span class="point-icon"></span>Commodity<br>Pricing</div>
  </section>

  <div class="watermark-name">Bent Cedar</div>

  <div class="address-rule" style="top:441px;width:512px"></div>
  <div class="address-rule" style="top:516px;width:512px"></div>
  <div class="address-rule" style="top:590px;width:512px"></div>
  <div class="address-rule" style="top:664px;width:512px"></div>
  <div class="address-rule" style="top:738px;width:309px"></div>
</main>
</body>
</html>
```